Mortgage Broker needs a DL leaflet design (both sides)

I need a leaflet design that I will be dropping off in mailboxes to people who are renting their house or unit and looking to borrow money to buy their own home (eg Direct Mail)
It needs to be eye catching, and grab their attention quickly.My job is to arrange the home loan for them so target market is twofold :-
1. People who have decided to buy and have not yet decided how to raise the money, and
2. People who were thinking about buying and the leaflet will trigger action to be taken.
I have some existing logos and images to be used which are consistent with my website (brightkeyfinance.com.au).
My core colour designs are Black, White & Green.
I have done a mock example via Publisher to give an idea of what I am looking for (word content OK but design needs a lot of work !)
Target Market(s)
Home buyers, principally young couples looking to buy a house or unit for their own occupation.
Industry/Entity Type
House
Requirements
Must have
- 2 Pages and must include my Logo (I have attached 3 designs), Contact details (Name, Mobile, Email Address, and Website). Text as written on the attache dmock design (font size and location of text can change). It must be DL sized (front & back) that I will have printed on decent quality paper. Credit Licencing details attached on mock design must be included but in lower case (at least on one side of the design).
Nice to have
- I had a previous designer complete a Double DL brochure (file is attached called Doctors Double DL brochure) which I liked the idea of having the leaves from my logo appearing as a watermark in the background.
Should not have
- It must look clear and concise. Not too much competing imagery that might distract the reader. Not too "busy" or crammed.

```html
<!DOCTYPE html>
<html lang="en">
<head>
<meta charset="utf-8">
<title>Brightkey Finance DL Leaflet</title>
<link rel="stylesheet" href="https://fonts.googleapis.com/css2?family=Arimo:wght@400;700&family=Lato:wght@300;400&family=Roboto+Condensed:wght@700&family=Signika:wght@400&display=swap">
<style>
:root{
  --page-bg:#e1e4e9;
  --green-deep:#1f7a2c;
  --green-mid:#3aa346;
  --green-bright:#5cc04a;
  --green-line:#8dd05a;
  --green-text:#7dc242;
  --star-green:#3a8f46;
  --ink:#2f2f2f;
  --body-ink:#3a3a3a;
  --footer-dark:#2a2c2b;
  --front-dark:#253028;
  --photo-blue:#4a6f9e;
  --photo-teal:#5d7a72;
  --label-grey:#9b9b9b;
  --label-red:#e0262c;
  --white:#ffffff;
}
*{box-sizing:border-box;margin:0;padding:0}
html,body{width:1085px;height:1200px;overflow:hidden;background:var(--page-bg)}
.stage{position:absolute;left:0;top:0;width:1200px;height:1327px;transform:scale(0.904);transform-origin:0 0;font-family:"Arimo",Arial,sans-serif}
.stage-title{position:absolute;top:8px;left:0;width:1200px;text-align:center;color:var(--label-red);font-size:27px}
.side-label{position:absolute;top:1252px;color:var(--label-grey);font-size:34px;transform:translateX(-50%)}
.panel{position:absolute;top:50px;width:566px;height:1191px;overflow:hidden;border:1px solid #6c6c6c}
.panel-back{left:27px;background:linear-gradient(180deg,#eef4ee 0%,#f3f5f3 40%,#e9ebea 100%)}
.panel-front{left:607px;background:linear-gradient(180deg,#1f6e2b 0%,#2b8a38 40%,#24402b 75%,var(--front-dark) 100%)}
.band-top{position:absolute;left:0;top:0;width:100%;height:122px;background:radial-gradient(ellipse at 70% 0%,var(--green-bright) 0%,var(--green-mid) 45%,var(--green-deep) 100%)}
.rule{position:absolute;left:0;width:100%;height:8px;background:var(--green-line)}
.starburst{position:absolute;left:113px;top:88px;width:340px;height:185px}
.starburst-text{position:absolute;left:113px;top:134px;width:340px;text-align:center;color:var(--star-green);font-family:"Roboto Condensed",Arial,sans-serif;font-weight:700;font-size:28px;line-height:35px}
.repay-heading{position:absolute;left:35px;top:343px;font-family:"Roboto Condensed",Arial,sans-serif;font-weight:700;font-size:29px;color:var(--ink)}
.repay-bar{position:absolute;left:36px;width:493px;height:37px;color:var(--white);font-family:"Signika",Arial,sans-serif;font-size:26px;line-height:37px;text-align:center;word-spacing:6px}
.bar-250{top:402px;background:linear-gradient(90deg,#3ec0cf 0%,#237c8a 45%,#1d2a33 100%)}
.bar-350{top:443px;background:linear-gradient(90deg,#1d2422 0%,#233027 50%,#7bbf3f 100%)}
.bar-400{top:483px;background:linear-gradient(90deg,#c8236b 0%,#8a1f4f 50%,#3a1c2a 100%)}
.bar-500{top:524px;background:linear-gradient(90deg,#d87a2b 0%,#7a4a2a 50%,#3a2a22 100%)}
.back-copy{position:absolute;left:36px;top:590px;width:494px;color:var(--body-ink);font-size:18px;line-height:23px;text-align:justify}
.back-copy p{margin-bottom:22px}
.money-house{position:absolute;left:43px;top:925px;width:225px;height:200px;border-radius:8px;background:linear-gradient(160deg,#d9d8cc 0%,#b8a868 55%,#a88a2e 100%)}
.brand-back{position:absolute;left:300px;top:1000px;width:240px;text-align:right}
.brand-name{font-family:"Lato",Arial,sans-serif;font-weight:300;white-space:nowrap}
.brand-back .brand-name{font-size:30px;color:#3b3b3b}
.brand-sub{font-family:"Lato",Arial,sans-serif;letter-spacing:3px;color:var(--green-mid)}
.brand-back .brand-sub{font-size:11px;margin-top:4px;text-align:center;padding-left:40px}
.back-footer{position:absolute;left:0;top:1070px;width:100%;height:121px;background:var(--footer-dark)}
.contact-list{position:absolute;left:244px;top:1090px;list-style:none;color:var(--white);font-size:19px}
.contact-list li{display:flex;align-items:center;height:30px}
.contact-list svg{width:20px;height:20px;margin-right:10px;flex:none}
.headline{position:absolute;left:0;top:62px;width:100%;text-align:center;color:var(--white);font-family:"Roboto Condensed",Arial,sans-serif;font-weight:700;text-shadow:0 2px 6px rgba(0,0,0,.35)}
.headline .line-1{display:block;font-size:66px;line-height:74px}
.headline .line-2{display:block;font-size:70px;line-height:80px}
.front-photo{position:absolute;left:0;top:245px;width:100%;height:388px;background:linear-gradient(180deg,var(--photo-blue) 0%,var(--photo-teal) 100%)}
.front-copy{position:absolute;left:38px;top:734px;width:500px;color:var(--white);font-size:18px;line-height:23px}
.front-copy p{margin-bottom:24px}
.tagline{position:absolute;left:38px;top:972px;color:var(--green-text);font-family:"Arimo",Arial,sans-serif;font-weight:700;font-size:34px;line-height:45px}
.front-web{position:absolute;left:38px;top:1064px;color:var(--white);font-family:"Roboto Condensed",Arial,sans-serif;font-weight:700;font-size:28px;letter-spacing:1px}
.brand-front{position:absolute;left:383px;top:1062px;width:170px;text-align:center}
.brand-front .brand-name{font-size:21px;color:var(--white)}
.brand-front .brand-sub{font-size:7px;margin-top:2px}
.front-footer{position:absolute;left:0;top:1130px;width:100%;height:61px;background:linear-gradient(90deg,#2e9a3b,#4fb548 50%,#2e9a3b);color:var(--white);font-size:13px;line-height:16px;text-align:center;padding-top:19px}
</style>
</head>
<body>
<div class="stage">
  <div class="stage-title">Revised Design _R1 with images</div>

  <section class="panel panel-back">
    <div class="band-top"></div>
    <div class="rule" style="top:122px"></div>

    <svg class="starburst" viewBox="0 0 340 185" aria-hidden="true">
      <polygon fill="#ffffff" stroke="#3a8f46" stroke-width="5" stroke-linejoin="miter"
        points="170,8 195,32 235,12 245,42 290,32 285,60 330,68 305,92 332,118 290,125 300,155 252,148 240,178 200,158 170,180 140,158 100,178 88,148 40,155 50,125 8,118 35,92 10,68 55,60 50,32 95,42 105,12 145,32"/>
    </svg>
    <div class="starburst-text">How much can<br>I afford to<br>borrow ?</div>

    <h2 class="repay-heading">Indicative Weekly Loan Repayments</h2>
    <div class="repay-bar bar-250">$250 per week = $200,000</div>
    <div class="repay-bar bar-350">$350 per week = $282,000</div>
    <div class="repay-bar bar-400">$400 per week = $320,000</div>
    <div class="repay-bar bar-500">$500 per week = $400,000</div>

    <div class="back-copy">
      <p>The above amounts are based on a term of 30 years, and an Interest Rate of 5.00%. Interest Rates may fluctuate over time.</p>
      <p>These are Indicative amounts only. You should ensure any loan you apply for does not place you under any undue hardship.</p>
      <p>If you can comfortably afford this level of commitment, contact me so I can assess your borrowing capacity from a variety of lenders.</p>
    </div>

    <div class="brand-back">
      <div class="brand-name">Brightkey Finance</div>
      <div class="brand-sub">GOLD COAST</div>
    </div>

    <div class="rule" style="top:1058px"></div>
    <div class="back-footer"></div>
    <div class="money-house" role="img" aria-label="House built from banknotes on a bed of gold coins"></div>

    <ul class="contact-list">
      <li><svg viewBox="0 0 20 20" aria-hidden="true"><rect x="5" y="1" width="10" height="18" rx="2" fill="#fff"/><rect x="7" y="3" width="6" height="6" fill="#2a2c2b"/></svg>0400 318 275</li>
      <li><svg viewBox="0 0 20 20" aria-hidden="true"><rect x="1" y="4" width="18" height="12" fill="none" stroke="#fff" stroke-width="1.6"/><path d="M1 4 L10 11 L19 4" fill="none" stroke="#fff" stroke-width="1.6"/></svg>daniel@brightkeyfinance.com.au</li>
      <li><svg viewBox="0 0 20 20" aria-hidden="true"><circle cx="10" cy="10" r="8.5" fill="none" stroke="#fff" stroke-width="1.6"/><path d="M1.5 10 H18.5 M10 1.5 C5 6 5 14 10 18.5 M10 1.5 C15 6 15 14 10 18.5" fill="none" stroke="#fff" stroke-width="1.3"/></svg>brightkeyfinance.com.au</li>
    </ul>
  </section>

  <section class="panel panel-front">
    <div class="band-top" style="height:237px"></div>
    <h1 class="headline"><span class="line-1">Want to</span><span class="line-2">Stop Renting ?</span></h1>
    <div class="rule" style="top:237px"></div>
    <div class="front-photo" role="img" aria-label="Waterfront homes and moored boats, overlaid with 3D lettering reading Home Loans Mortgage Financing"></div>
    <div class="rule" style="top:633px"></div>

    <div class="front-copy">
      <p>Do you think now is a good time to buy a house or a unit ?</p>
      <p>Do you realise you only need a very small deposit ?</p>
      <p>Do you want to know how much you are able to borrow ?</p>
      <p>Brightkey Finance are accredited with many banks so we can source the most appropriate loan for you, which will save you time, and help make home ownership a reality.</p>
    </div>

    <div class="tagline">We are local.<br>We can help.</div>
    <div class="front-web">brightkeyfinance.com.au</div>
    <div class="brand-front">
      <div class="brand-name">Brightkey Finance</div>
      <div class="brand-sub">GOLD COAST</div>
    </div>

    <div class="front-footer">Brightkey Finance Gold Coast are Authorised Credit Representative under Australian<br>Credit Licence 512804 issued by ASIC.</div>
  </section>

  <div class="side-label" style="left:310px">back</div>
  <div class="side-label" style="left:600px">4x8 inches</div>
  <div class="side-label" style="left:890px">front</div>
</div>
</body>
</html>
```